sydney wedding photography business needs a business card design

we need a business card design for a sydney based wedding photography and videography business. our business name is :golden hour studio and film. our target clients are 24-35 yrs female. our style is candid, organic, natural, dynamic. we are a team of young photographers and videographers, and help brides to create memories that they will cherish for the rest of their lives. the logo will be provided. we want an elegant design that reflects our style, and also want to give a great impression to our clients that we are one of the best studios in sydney and our brand means quality and premium service.

Target Market(s)

bride to be, 24-35 years old, living in sydney and surrunding areas

Industry/Entity Type

Wedding Photography

Contact Information for Business Card

address: 57 tarrant street, glenmore nsw 2047
mobile: 0431872259
phone: (02) 9163 2408
info@tidewillowstudio.net.au
www.tidewillowstudio.net.au
facebook:tidewillowweddings
instagram:tidewillowweddings

Font styles to use
Serif
Sans Serif

Requirements
Nice to have
• maybe add my slogan"memories beyond eternity" if the layout looks good
Should not have
• no black color, not good idea for wedding biz card

```html
<!DOCTYPE html>
<html lang="en">
<head>
<meta charset="utf-8">
<title>Golden Hour Studio and Film – Business Card</title>
<link rel="stylesheet" href="https://fonts.googleapis.com/css2?family=Raleway:wght@400;500&display=swap">
<style>
  :root {
    --page: #ece8e1;
    --card-front-light: #5a4330;
    --card-front-mid: #46331f;
    --card-front-deep: #3a2a1b;
    --gold: #e0ac2a;
    --gold-deep: #a8760c;
    --gold-light: #e8bb3c;
    --ink-light: #f3ece0;
    --mark-faint: rgba(255, 240, 210, 0.07);
  }
  * { box-sizing: border-box; margin: 0; padding: 0; }
  html, body {
    width: 1200px;
    height: 950px;
    overflow: hidden;
    background: var(--page);
    font-family: "Raleway", sans-serif;
  }
  .stage {
    width: 1200px;
    height: 950px;
    display: flex;
    flex-direction: column;
    align-items: center;
    justify-content: center;
    gap: 50px;
  }
  .card {
    position: relative;
    width: 700px;
    height: 400px;
    overflow: hidden;
    box-shadow: 0 6px 18px rgba(0, 0, 0, 0.18);
  }
  .card--front {
    background: linear-gradient(135deg, var(--card-front-light) 0%, var(--card-front-mid) 55%, var(--card-front-deep) 100%);
  }
  .card--back {
    background: linear-gradient(135deg, var(--gold-light) 0%, var(--gold) 50%, var(--gold-deep) 100%);
  }
  .brand-mark-area {
    position: absolute;
    left: 40px;
    top: 40px;
    width: 190px;
    height: 190px;
  }
  .brand {
    position: absolute;
    right: 90px;
    top: 58px;
    text-align: center;
    color: var(--gold);
    font-weight: 500;
  }
  .brand__name {
    font-size: 38px;
    letter-spacing: 1px;
    line-height: 1;
  }
  .brand__sub {
    margin-top: 8px;
    font-size: 12px;
    font-weight: 500;
    letter-spacing: 8px;
  }
  .rule {
    position: absolute;
    height: 1px;
    background: var(--gold);
  }
  .rule--top { left: 260px; right: 40px; top: 150px; }
  .rule--name { left: 40px; width: 330px; top: 298px; }
  .social {
    position: absolute;
    right: 40px;
    top: 116px;
    display: flex;
    gap: 6px;
  }
  .social__dot {
    width: 20px;
    height: 20px;
    border-radius: 50%;
    background: var(--gold);
  }
  .person {
    position: absolute;
    left: 40px;
    top: 260px;
    color: var(--gold);
    font-size: 26px;
    font-weight: 400;
    letter-spacing: 1px;
    line-height: 1.2;
  }
  .contacts {
    position: absolute;
    left: 40px;
    top: 312px;
    color: var(--ink-light);
    font-size: 13px;
    line-height: 1.6;
    list-style: none;
  }
  .contacts__label { color: var(--gold); }
  .contacts__gap { display: inline-block; width: 10px; }
</style>
</head>
<body>
<main class="stage">
  <section class="card card--front" aria-label="Business card front">
    <svg class="brand-mark-area" viewBox="0 0 190 190" role="img" aria-label="Faint brand symbol decoration">
      <circle cx="95" cy="95" r="93" fill="var(--mark-faint)"/>
    </svg>

    <div class="brand">
      <div class="brand__name">GOLDEN HOUR</div>
      <div class="brand__sub">STUDIO AND FILM</div>
    </div>

    <div class="social" aria-label="Social links">
      <span class="social__dot"></span>
      <span class="social__dot"></span>
    </div>
    <div class="rule rule--top"></div>

    <h1 class="person">CLARA WENDT</h1>
    <div class="rule rule--name"></div>

    <ul class="contacts">
      <li><span class="contacts__label">P :</span> (02) 9163 2408<span class="contacts__gap"></span><span class="contacts__label">M :</span> 0431 872 259</li>
      <li><span class="contacts__label">E :</span> info@tidewillowstudio.net.au<span class="contacts__gap"></span><span class="contacts__label">W :</span> tidewillowstudio.net.au</li>
      <li><span class="contacts__label">A :</span> 57 tarrant street, glenmore nsw 2047</li>
    </ul>
  </section>

  <section class="card card--back" aria-label="Business card back"></section>
</main>
</body>
</html>
```